Web Developer Needs a Business Card Design

I need a personal business card design that represents me as a web developer for potential employers. I would like the background to be a dark color on the front for contrast with my logo and name. The back will have all my information along with a smaller version of the logo. I want something with a modern look and feel, not too conservative. This will be used for potential employers and freelance work.

Industry/Entity Type

Business

Contact Information for Business Card

Front should have my logo and name. The back should have all my personal information which would include: name: Tom Varulek, phone: 570-614-3098, email: tomvarulek@quillbox.net, website url: www.tomvarulek.net, logo, web developer.

Font styles to use
Sans Serif

Requirements
Must have
• Must include my logo. The color palette base color will be the logo color.

```html
<!DOCTYPE html>
<html lang="en">
<head>
<meta charset="utf-8">
<title>Tom Varulek – Business Card</title>
<link rel="stylesheet" href="https://fonts.googleapis.com/css2?family=Open+Sans:wght@400;600&display=swap">
<style>
  :root {
    --teal: #6fcdb8;
    --teal-light: #82d4c1;
    --ink: #121212;
    --ink-soft: #1c1c1c;
    --page: #e9e7e3;
    --text-dark: #0d0d0d;
  }
  * { box-sizing: border-box; margin: 0; padding: 0; }
  html, body {
    width: 1200px;
    height: 892px;
    overflow: hidden;
    background: var(--page);
    font-family: "Open Sans", Arial, sans-serif;
  }
  .canvas {
    position: relative;
    width: 1200px;
    height: 892px;
  }
  .card {
    position: absolute;
    width: 540px;
    height: 330px;
    border-radius: 4px;
    overflow: hidden;
    box-shadow: 0 10px 28px rgba(0,0,0,0.22);
  }
  .card-front {
    left: 610px;
    top: 110px;
    background: var(--ink);
  }
  .card-back {
    left: 50px;
    top: 450px;
  }
  .card-art {
    position: absolute;
    inset: 0;
    width: 100%;
    height: 100%;
  }
  .front-name {
    position: absolute;
    left: 0;
    right: 0;
    top: 228px;
    text-align: center;
    color: var(--teal);
    font-size: 38px;
    font-weight: 600;
    letter-spacing: 0.5px;
  }
  .identity {
    position: absolute;
    left: 36px;
    top: 186px;
    color: var(--text-dark);
  }
  .identity .name {
    font-size: 31px;
    font-weight: 600;
    line-height: 1.05;
  }
  .identity .role {
    font-size: 18px;
    font-weight: 600;
    line-height: 1.2;
  }
  .contacts {
    position: absolute;
    left: 282px;
    top: 210px;
    list-style: none;
    color: var(--text-dark);
  }
  .contacts li {
    display: flex;
    align-items: center;
    gap: 12px;
    height: 30px;
    font-size: 17px;
    font-weight: 600;
    white-space: nowrap;
  }
  .contacts .icon {
    width: 18px;
    height: 18px;
    flex: none;
  }
</style>
</head>
<body>
<main class="canvas">

  <section class="card card-front" aria-label="Card front">
    <svg class="card-art" viewBox="0 0 540 330" aria-hidden="true">
      <circle cx="270" cy="118" r="80" fill="none" stroke="var(--teal)" stroke-width="9"/>
    </svg>
    <p class="front-name">Tom Varulek</p>
  </section>

  <section class="card card-back" aria-label="Card back">
    <svg class="card-art" viewBox="0 0 540 330" aria-hidden="true">
      <rect width="540" height="330" fill="var(--ink)"/>
      <path d="M0,84 Q260,176 540,194 L540,330 L0,330 Z" fill="var(--teal)"/>
      <circle cx="280" cy="84" r="58" fill="none" stroke="var(--teal)" stroke-width="7"/>
      <line x1="258" y1="198" x2="258" y2="310" stroke="var(--text-dark)" stroke-width="2"/>
    </svg>

    <div class="identity">
      <p class="name">Tom Varulek</p>
      <p class="role">web developer</p>
    </div>

    <ul class="contacts">
      <li>
        <svg class="icon" viewBox="0 0 18 18" aria-hidden="true">
          <rect width="18" height="18" rx="2" fill="var(--ink-soft)"/>
          <path d="M6 4 L8 6.5 L6.8 8 Q8 10.5 10 11.2 L11.5 10 L14 12 L12.8 14 Q7.5 14 4.5 8 Q4.5 5.2 6 4 Z" fill="var(--teal)"/>
        </svg>
        <span>570-614-3098</span>
      </li>
      <li>
        <svg class="icon" viewBox="0 0 18 18" aria-hidden="true">
          <rect width="18" height="18" rx="2" fill="var(--ink-soft)"/>
          <circle cx="9" cy="9" r="5" fill="none" stroke="var(--teal)" stroke-width="1.4"/>
          <ellipse cx="9" cy="9" rx="2" ry="5" fill="none" stroke="var(--teal)" stroke-width="1.1"/>
          <line x1="4" y1="9" x2="14" y2="9" stroke="var(--teal)" stroke-width="1.1"/>
        </svg>
        <span>www.tomvarulek.net</span>
      </li>
      <li>
        <svg class="icon" viewBox="0 0 18 18" aria-hidden="true">
          <rect width="18" height="18" rx="2" fill="var(--ink-soft)"/>
          <rect x="3.5" y="5.5" width="11" height="7.5" fill="none" stroke="var(--teal)" stroke-width="1.3"/>
          <path d="M3.5 5.5 L9 10 L14.5 5.5" fill="none" stroke="var(--teal)" stroke-width="1.3"/>
        </svg>
        <span>tomvarulek@quillbox.net</span>
      </li>
    </ul>
  </section>

</main>
</body>
</html>
```